Website Re-design

Hi, I'm looking for help in redesigning my web site. I currently have a site www.brightferncove.example where I sell lamps, and while I like some aspects of the design, you can tell that I have done the graphics myself and am not a pro at it. I'd like help in redesigning it, and am open to completely new design graphics. I have made the 3 slider images myself, and I feel they could be a bit better, but I am not sure how to do it. For example, on the homepage, the 'About Us', 'Secured Shopping', and '$10 Off' graphics don't go well with the rest of the page. I would like more cohesion in the design and more visual interest in the header, which is pretty basic right now. Also, that the bottom footer is black, I would like instead something else. I am looking for just the layout of the homepage, and possibly once that is done to work on more visual interest in some of the informational pages and product pages. I am looking for just the design in the form of a photoshop file or files that I can incorporate into my site. Thank you!
Updates

Project Deadline Extended
Reason: I just made this project payment committed, so I'd like a chance for designers who only choose payment committed projects to submit artwork. Thank you.

This project is now payment guaranteed/ committed.  Thanks.

Industry/Entity Type

Shopping

```html
<!DOCTYPE html>
<html lang="en">
<head>
<meta charset="utf-8">
<title>Bright Fern Cove — Home</title>
<link rel="stylesheet" href="https://fonts.googleapis.com/css2?family=Open+Sans:wght@400;600;700&family=Kaushan+Script&family=Norican&family=Tinos&display=swap">
<style>
:root{
  --ink:#3b3b3b;
  --muted:#555;
  --brown:#4a3a34;
  --topbar:#ececec;
  --line:#d9d9d9;
  --page:#f4f4f2;
  --teal:#4fb3c8;
  --red:#e42228;
  --green:#74b56a;
  --price:#d21f1f;
  --dark:#111;
}
*{box-sizing:border-box;margin:0;padding:0}
html,body{width:784px;height:1200px;overflow:hidden}
body{position:relative;background:var(--page);font-family:"Open Sans",Arial,sans-serif;color:var(--ink)}
.abs{position:absolute}
/* top bar */
.topbar{left:0;top:0;width:784px;height:34px;background:var(--topbar)}
.account-links{left:390px;top:10px;font-size:8px;color:var(--ink);display:flex;gap:10px;white-space:nowrap}
.account-links b{font-weight:700}
.search{left:582px;top:7px;width:102px;height:19px;border-radius:10px;background:#fff;border:1px solid #ccc;font-size:8px;padding:4px 8px}
.search svg{position:absolute;right:6px;top:4px}
/* header */
.header{left:0;top:34px;width:784px;height:83px;background:#fff}
.brand{left:104px;top:53px;display:flex;align-items:center;gap:8px;font-size:17px;font-weight:600;color:var(--ink);line-height:1;white-space:nowrap}
.brand i{display:block;width:34px;height:34px;border:2px solid var(--ink);border-radius:4px}
.cart{left:482px;top:47px;font-size:9px;color:var(--muted);display:flex;align-items:center;gap:5px;white-space:nowrap}
.cart-count{left:569px;top:42px;width:28px;height:28px;border-radius:50%;border:1.5px solid #777;font-size:8px;color:var(--price);text-align:center;line-height:26px}
.items{left:603px;top:50px;font-size:9px;color:var(--muted)}
.checkout{left:631px;top:46px;width:61px;height:19px;border:1px solid #bbb;border-radius:3px;background:linear-gradient(#fafafa,#e2e2e2);font-size:9px;text-align:center;line-height:17px;color:var(--ink)}
.nav{left:396px;top:74px;width:297px;height:31px;border:1px solid var(--line);display:flex;justify-content:space-around;align-items:center;font-size:11px;color:var(--muted);letter-spacing:.2px}
/* hero */
.hero{left:0;top:117px;width:784px;height:423px;background:linear-gradient(180deg,#fbfbfb 0%,#ececec 70%,#d8d8d8 72%,#efefef 100%)}
.hero-photo{left:436px;top:157px;width:236px;height:327px;background:linear-gradient(180deg,#5a5a5a 0%,#6c6c6c 45%,#b9b9bc 47%,#9d9da1 80%,#cfcfd1 100%)}
.slogan{left:104px;top:145px;width:250px;text-align:center;font-family:"Kaushan Script",cursive;color:#2b1e1a;line-height:1}
.slogan .l1{font-size:50px}
.slogan .l2{font-size:30px;margin-top:2px;position:relative}
.slogan .l2::before,.slogan .l2::after{content:"";position:absolute;top:2px;width:80px;height:3px;border-top:1px solid #bbb;border-bottom:1px solid #bbb}
.slogan .l2::before{left:0}.slogan .l2::after{right:0}
.slogan .l3{font-size:50px;margin-top:2px}
.slide-title{left:90px;top:318px;font-family:"Tinos",serif;font-size:19px;color:#333;white-space:nowrap}
.shop-btn{left:146px;top:360px;width:166px;height:36px;border-radius:4px;background:linear-gradient(#f3692c,#d8420f);border-bottom:2px solid #a93008;font-family:"Tinos",serif;font-size:18px;color:#fff;text-align:center;line-height:34px}
.dots{left:215px;top:429px;display:flex;gap:3px}
.dots i{width:7px;height:7px;border-radius:50%;background:#eee;border:1px solid #ccc}
.dots i.on{background:#111;border-color:#111}
/* features */
.feature{top:518px;width:188px}
.feature svg{display:block}
.feature h2{position:absolute;left:0;top:52px;width:188px;text-align:center;font-family:"Kaushan Script",cursive;font-weight:400;font-size:21px;color:#fff;white-space:nowrap}
.feature p{position:absolute;left:-6px;top:104px;width:200px;text-align:center;font-size:10px;line-height:14px;color:var(--muted)}
.feature a{position:absolute;top:159px;height:18px;font-size:8px;color:#fff;text-align:center;line-height:18px;text-decoration:none}
/* products */
.section-title{left:0;top:722px;width:784px;text-align:center;font-family:"Norican",cursive;font-weight:400;font-size:23px;color:var(--brown)}
.squiggle{left:325px;top:755px}
.product{top:778px;width:137px}
.product .photo{width:137px;height:161px;border:1px solid #ddd;background:#fff;padding:3px}
.product .photo div{width:100%;height:100%;background:linear-gradient(180deg,#f2f2f2 0%,#e6e6e6 80%,#fafafa 82%,#f4f4f4 100%)}
.product h3{font-weight:400;font-size:9px;margin-top:8px;color:var(--ink);white-space:nowrap;line-height:12px}
.product .price{font-size:9px;color:var(--price);line-height:12px}
.divider{left:98px;top:990px}
.view-more{left:358px;top:982px;width:68px;height:18px;border:1px solid #ccc;background:#f7f7f7;font-size:9px;color:#777;text-align:center;line-height:16px}
/* footer */
.footer{left:0;top:1025px;width:784px;height:175px;background:linear-gradient(135deg,#e8e8e8,#dedede 50%,#e9e9e9)}
.fcol{top:1046px;width:87px}
.fcol h4{font-size:9px;font-weight:400;color:var(--dark);padding-bottom:4px;border-bottom:1px solid #c9c9c9;margin-bottom:3px;letter-spacing:.2px}
.fcol li{list-style:none;font-size:8.5px;line-height:15.3px;color:#444;white-space:nowrap}
.signup{left:529px;top:1046px;width:164px}
.signup h4{font-size:7.8px;font-weight:400;color:var(--dark);white-space:nowrap;line-height:12px}
.signup-form{display:flex;margin-top:7px;height:21px}
.signup-form span{width:113px;background:#fff;border:1px solid #222;font-size:7.5px;padding:5px 5px;color:#333}
.signup-form b{width:51px;background:var(--dark);color:#fff;font-size:8.5px;line-height:21px;padding-left:6px;clip-path:polygon(0 0,80% 0,100% 50%,80% 100%,0 100%)}
.signup p{font-size:8.5px;color:#444;margin-top:6px;white-space:nowrap}
.social{display:flex;gap:6px;margin-top:11px}
.social i{display:block;width:27px;height:27px;border-radius:7px}
.copy-line{left:91px;top:1167px;width:601px;border-top:1px solid #cfcfcf}
.copyright{left:0;top:1178px;width:784px;text-align:center;font-size:8px;color:#333}
</style>
</head>
<body>
  <div class="abs topbar"></div>
  <div class="abs account-links"><b>Sign In</b><span>or</span><span>Create an account</span><span>My Account</span></div>
  <div class="abs search">Search
    <svg width="11" height="11" viewBox="0 0 11 11"><circle cx="4.5" cy="4.5" r="3.3" fill="none" stroke="#888" stroke-width="1.4"/><line x1="7" y1="7" x2="10" y2="10" stroke="#888" stroke-width="1.6"/></svg>
  </div>

  <div class="abs header"></div>
  <div class="abs brand"><i></i><span>Bright Fern Cove</span></div>
  <div class="abs cart">
    <svg width="18" height="14" viewBox="0 0 18 14"><path d="M1 1h3l2 8h9l2-6H5" fill="none" stroke="#2a9db5" stroke-width="1.6"/><circle cx="7" cy="12" r="1.3" fill="#2a9db5"/><circle cx="14" cy="12" r="1.3" fill="#2a9db5"/></svg>
    Shopping Cart
  </div>
  <div class="abs cart-count">0</div>
  <div class="abs items">Items</div>
  <div class="abs checkout">Checkout</div>
  <nav class="abs nav"><span>HOME</span><span>SHOP</span><span>ABOUT US</span><span>CONTACT US</span></nav>

  <div class="abs hero" role="img" aria-label="Bright white room with pale wooden floorboards"></div>
  <div class="abs hero-photo" role="img" aria-label="Photo of a smoke gray glass table lamp with a dark shade"></div>
  <div class="abs slogan"><div class="l1">Set</div><div class="l2">the</div><div class="l3">Mood</div></div>
  <div class="abs slide-title">"The Willa" Smoke Gray Table Lamp</div>
  <div class="abs shop-btn">SHOP ALL LAMPS</div>
  <div class="abs dots"><i></i><i class="on"></i><i></i></div>

  <section class="abs feature" style="left:98px">
    <svg width="188" height="92" viewBox="0 0 188 92">
      <rect x="0" y="25" width="188" height="3" fill="#8fd0de"/>
      <path d="M0 28h188v58l-4 4-4-4-4 4-4-4-4 4-4-4-4 4-4-4-4 4-4-4-4 4-4-4-4 4-4-4-4 4-4-4-4 4-4-4-4 4-4-4-4 4-4-4-4 4-4-4-4 4-4-4-4 4-4-4-4 4-4-4-4 4-4-4-4 4-4-4-4 4-4-4-4 4-4-4-4 4-4-4-4 4-4-4-4 4-4-4-4 4-4-4-4 4-4-4-4 4-4-4-4 4-4-4-4 4-4-4-4 4-4-4-4 4-4-4-4 4-4-4-4 4-4-4-4 4-4-4-4 4-4-4-4 4-4-4-4 4-4-4-4 4-4-4-4 4-4-4-4 4-4-4-4 4-4-4-4 4-4-4-4 4z" fill="var(--teal)"/>
      <polygon points="94,1 116,13 116,37 94,49 72,37 72,13" fill="#fff"/>
      <polygon points="94,5 112,15 112,35 94,45 76,35 76,15" fill="var(--teal)"/>
      <circle cx="94" cy="20" r="4" fill="#fff"/><path d="M86 33a8 7 0 0 1 16 0z" fill="#fff"/>
    </svg>
    <h2>About Us</h2>
    <p>Bright Fern Cove provides beautiful and artistic home and hospitality lighting.</p>
    <a href="#" style="left:64px;width:60px;background:var(--teal)">READ MORE</a>
  </section>

  <section class="abs feature" style="left:298px">
    <svg width="188" height="92" viewBox="0 0 188 92">
      <rect x="0" y="25" width="188" height="3" fill="#f07f82"/>
      <path d="M0 28h188v58l-4 4-4-4-4 4-4-4-4 4-4-4-4 4-4-4-4 4-4-4-4 4-4-4-4 4-4-4-4 4-4-4-4 4-4-4-4 4-4-4-4 4-4-4-4 4-4-4-4 4-4-4-4 4-4-4-4 4-4-4-4 4-4-4-4 4-4-4-4 4-4-4-4 4-4-4-4 4-4-4-4 4-4-4-4 4-4-4-4 4-4-4-4 4-4-4-4 4-4-4-4 4-4-4-4 4-4-4-4 4-4-4-4 4-4-4-4 4-4-4-4 4-4-4-4 4-4-4-4 4-4-4-4 4-4-4-4 4-4-4-4 4-4-4-4 4-4-4-4 4-4-4-4 4-4-4-4 4z" fill="var(--red)"/>
      <polygon points="94,1 116,13 116,37 94,49 72,37 72,13" fill="#fff"/>
      <polygon points="94,5 112,15 112,35 94,45 76,35 76,15" fill="var(--red)"/>
      <path d="M82 18h3l2 9h8l2-6H86" fill="none" stroke="#fff" stroke-width="1.6"/>
      <circle cx="88" cy="30" r="1.2" fill="#fff"/><circle cx="94" cy="30" r="1.2" fill="#fff"/>
      <rect x="98" y="23" width="9" height="7" fill="#fff"/><path d="M100 23v-3a2.5 2.5 0 0 1 5 0v3" fill="none" stroke="#fff" stroke-width="1.4"/>
    </svg>
    <h2>Secured Shopping</h2>
    <p>Shopping at Bright Fern Cove is secured and protected by industry standard best practices.</p>
    <a href="#" style="left:64px;width:60px;background:var(--red)">READ MORE</a>
  </section>

  <section class="abs feature" style="left:498px">
    <svg width="188" height="92" viewBox="0 0 188 92">
      <rect x="0" y="25" width="188" height="3" fill="#a9d6a2"/>
      <path d="M0 28h188v58l-4 4-4-4-4 4-4-4-4 4-4-4-4 4-4-4-4 4-4-4-4 4-4-4-4 4-4-4-4 4-4-4-4 4-4-4-4 4-4-4-4 4-4-4-4 4-4-4-4 4-4-4-4 4-4-4-4 4-4-4-4 4-4-4-4 4-4-4-4 4-4-4-4 4-4-4-4 4-4-4-4 4-4-4-4 4-4-4-4 4-4-4-4 4-4-4-4 4-4-4-4 4-4-4-4 4-4-4-4 4-4-4-4 4-4-4-4 4-4-4-4 4-4-4-4 4-4-4-4 4-4-4-4 4-4-4-4 4-4-4-4 4-4-4-4 4-4-4-4 4-4-4-4 4-4-4-4 4-4-4-4 4z" fill="var(--green)"/>
      <polygon points="94,1 116,13 116,37 94,49 72,37 72,13" fill="#fff"/>
      <polygon points="94,5 112,15 112,35 94,45 76,35 76,15" fill="var(--green)"/>
      <rect x="84" y="18" width="20" height="14" fill="#fff"/><path d="M84 18l10 8 10-8" fill="none" stroke="var(--green)" stroke-width="1.4"/>
    </svg>
    <h2>$10 Off</h2>
    <p>$10 off any purchase when you sign up for our newsletter.</p>
    <a href="#" style="left:64px;width:60px;background:var(--green)">SIGN UP</a>
  </section>

  <h2 class="abs section-title">Our Products</h2>
  <svg class="abs squiggle" width="134" height="5" viewBox="0 0 134 5"><path d="M0 2.5q2-2 4 0t4 0 4 0 4 0 4 0 4 0 4 0 4 0 4 0 4 0 4 0 4 0 4 0 4 0 4 0 4 0 4 0 4 0 4 0 4 0 4 0 4 0 4 0 4 0 4 0 4 0 4 0 4 0 4 0 4 0 4 0 4 0 4 0" fill="none" stroke="#bbb"/></svg>

  <article class="abs product" style="left:98px">
    <div class="photo"><div role="img" aria-label="Blue and green glass table lamp with white shade"></div></div>
    <h3>Lagoon Medium Table Lamp</h3><div class="price">$199.00</div>
  </article>
  <article class="abs product" style="left:249px">
    <div class="photo"><div role="img" aria-label="Purple faceted crystal table lamp with white shade"></div></div>
    <h3>Plum Facet Table Lamp</h3><div class="price">$219.00</div>
  </article>
  <article class="abs product" style="left:399px">
    <div class="photo"><div role="img" aria-label="Pierced silver porcelain table lamp with white shade"></div></div>
    <h3>Pebble Porcelain Table Lamp</h3><div class="price">$259.00</div>
  </article>
  <article class="abs product" style="left:549px">
    <div class="photo"><div role="img" aria-label="Sea green glass table lamp with white shade"></div></div>
    <h3>Tidewater Table Lamp</h3><div class="price">$179.00</div>
  </article>

  <svg class="abs divider" width="588" height="4" viewBox="0 0 588 4"><path d="M0 2 Q2 0 4 2 T8 2 T12 2 T16 2 T20 2 T24 2 T28 2 T32 2 T36 2 T40 2 T44 2 T48 2 T52 2 T56 2 T60 2 T64 2 T68 2 T72 2 T76 2 T80 2 T84 2 T88 2 T92 2 T96 2 T100 2 T104 2 T108 2 T112 2 T116 2 T120 2 T124 2 T128 2 T132 2 T136 2 T140 2 T144 2 T148 2 T152 2 T156 2 T160 2 T164 2 T168 2 T172 2 T176 2 T180 2 T184 2 T188 2 T192 2 T196 2 T200 2 T204 2 T208 2 T212 2 T216 2 T220 2 T224 2 T228 2 T232 2 T236 2 T240 2 T244 2 T248 2 T252 2 T256 2 T260 2 T264 2 T268 2 T272 2 T276 2 T280 2 T284 2 T288 2 T292 2 T296 2 T300 2 T304 2 T308 2 T312 2 T316 2 T320 2 T324 2 T328 2 T332 2 T336 2 T340 2 T344 2 T348 2 T352 2 T356 2 T360 2 T364 2 T368 2 T372 2 T376 2 T380 2 T384 2 T388 2 T392 2 T396 2 T400 2 T404 2 T408 2 T412 2 T416 2 T420 2 T424 2 T428 2 T432 2 T436 2 T440 2 T444 2 T448 2 T452 2 T456 2 T460 2 T464 2 T468 2 T472 2 T476 2 T480 2 T484 2 T488 2 T492 2 T496 2 T500 2 T504 2 T508 2 T512 2 T516 2 T520 2 T524 2 T528 2 T532 2 T536 2 T540 2 T544 2 T548 2 T552 2 T556 2 T560 2 T564 2 T568 2 T572 2 T576 2 T580 2 T584 2 T588 2" fill="none" stroke="#ccc"/></svg>
  <div class="abs view-more">View More</div>

  <footer>
    <div class="abs footer"></div>
    <div class="abs fcol" style="left:91px"><h4>HELP + INFO</h4><ul><li>Contact Us</li><li>Shipping Info</li><li>Returns</li><li>To The Trade</li><li>Privacy Policy</li><li>Terms of Use</li></ul></div>
    <div class="abs fcol" style="left:194px"><h4>MY ACCOUNT</h4><ul><li>Sign In</li><li>Order Status</li><li>Order History</li><li>View Cart</li><li>Checkout</li></ul></div>
    <div class="abs fcol" style="left:296px"><h4>ABOUT</h4><ul><li>Who We Are</li><li>Testimonials</li></ul></div>
    <div class="abs fcol" style="left:398px;width:120px"><h4 style="width:87px">CONTACT</h4><ul><li>Contact Us</li><li>info@brightferncove.example</li></ul></div>
    <div class="abs signup">
      <h4>SIGN UP FOR BRIGHT FERN COVE EMAILS</h4>
      <div class="signup-form"><span>Enter your email</span><b>JOIN US</b></div>
      <p>Because you love being the first to know</p>
      <div class="social">
        <i style="background:#3f86c9" role="img" aria-label="Social network link"></i>
        <i style="background:#3fa7dc" role="img" aria-label="Social network link"></i>
        <i style="background:#d8262d" role="img" aria-label="Social network link"></i>
      </div>
    </div>
    <div class="abs copy-line"></div>
    <div class="abs copyright">© 2013 Bright Fern Cove.&nbsp; All Rights Reserved</div>
  </footer>
</body>
</html>
```